Letterhead Design for Law Firm

**Edit: I have added the photo of a bottom that I like.

------
We are looking for a re-design of our new letterhead. The letterhead is for a law firm and will be used for digital and traditionally printed correspondence.

Here are some suggestions:

- Please use colours are #8ec900 and simple black.
- Please do not use any type of "waves" at the bottom of the page. This is not in style at all.
- Please stay modern yet conservative.
- Please use font Segoe UI Light or similar if you can
- Avoid clipart or illustrations.
- Utilize ample white space in the layout so the design looks clean and information is easy to read at a glance. Don't overcrowd the letterhead.
- Make sure the letterhead design is consistent with our brand identity (see corvelith.ca)
-Please, no black headers or footers.

I am attaching my current letterhead and signature for your convenience.

Remember, the letterhead is an extension of our professional identity. We are a successful firm and trial lawyers who correspond with insurers, judges, lawyers, courts, clients, etc. Make it new, modern, attractive, yet powerful and conservative.

It needs to be easily printable. I would like the bleed removed in print so the black bar the bottom crosses the page (but the text is not near the edges)
Updates

Low design quality

Target Market(s)

Clients, Government Offices, Judiciary, Lawyers, Insurance Companies, Colleagues.

Industry/Entity Type

Law

Other font styles liked:
• Segoe UI LIght, Calibri Light,

Colors
00AB8E
00BBA5
67D7C9
C6EFE9
E9F9F6

Requirements
Must have
• Everything that is on the letterhead now.
Nice to have
• Cutting Edge design, yet conservative.
Should not have
• law firm cliche design, images,

```html
<!DOCTYPE html>
<html lang="en">
<head>
<meta charset="utf-8">
<title>Corvelith Letterhead</title>
<link rel="stylesheet" href="https://fonts.googleapis.com/css2?family=Roboto:wght@300;400;500;700&display=swap">
<style>
:root{
  --green:#8ec900;
  --ink:#1c1c1c;
  --text:#2b2b2b;
  --muted:#555;
  --paper:#f7f5f5;
  --bar:#1e1e1e;
  --rule:#333;
}
*{margin:0;padding:0;box-sizing:border-box}
html,body{width:935px;height:1200px;overflow:hidden;background:var(--paper)}
body{font-family:"Roboto",Arial,sans-serif;color:var(--text);position:relative}
.abs{position:absolute}
.brand{left:0;width:935px;top:70px;text-align:center}
.brand-name{font-size:62px;font-weight:400;letter-spacing:2px;color:var(--ink);line-height:1}
.brand-tag{font-size:15px;font-weight:400;letter-spacing:2.5px;color:var(--ink);margin-top:6px}
.label{font-weight:500;font-size:15.5px;color:var(--ink)}
.prejudice{left:85px;top:181px}
.delivery{left:85px;top:230px}
.clerk{right:79px;top:184px;font-size:16.5px;text-align:right}
.clerk b{font-weight:500;color:var(--ink)}
.clerk span{color:var(--muted);font-weight:400}
.clerk-email{right:79px;top:206px;font-size:14.5px;display:flex;align-items:center;gap:6px}
.date{right:79px;top:236px;font-size:15px}
.recipient{left:85px;top:270px;font-size:16.5px;line-height:20px;color:var(--ink)}
.attention{left:84px;top:394px;font-size:16.5px;color:var(--ink)}
.salutation{left:84px;top:421px;font-size:16.5px;color:var(--ink)}
.re{left:85px;top:459px;font-size:16.5px;font-weight:700;color:var(--green)}
.matter{left:327px;top:492px;font-size:16.5px;line-height:20px;color:var(--ink)}
.rule{left:85px;top:573px;width:767px;height:1px;background:var(--rule)}
.body-copy{left:85px;top:598px;width:772px;font-size:12.4px;line-height:18px;font-weight:300;color:var(--text)}
.body-copy p+p{margin-top:18px}
.closing{left:86px;top:838px;font-size:14.5px;line-height:18px;color:var(--ink)}
.signature{left:86px;top:888px;width:240px;height:60px;background:linear-gradient(90deg,rgba(0,0,0,.06),rgba(0,0,0,.02))}
.signatory{left:88px;top:962px;font-size:14.5px;line-height:18px;color:var(--ink)}
.contact{left:83px;top:1080px;font-size:14.5px;line-height:19px;color:var(--ink)}
.contact div{display:flex;align-items:center;gap:5px}
.office{right:79px;top:1080px;font-size:15.5px;line-height:19px;text-align:right;color:var(--muted)}
.footer{left:0;top:1150px;width:935px;height:50px;background:var(--bar)}
.practice{left:85px;top:1156px;font-size:15px;line-height:18.5px;color:#fff}
.practice li{list-style:none;display:inline}
.practice li::before{content:"";display:inline-block;width:6px;height:6px;border-radius:50%;background:var(--green);margin:0 9px 2px 0;vertical-align:middle}
.practice li+li{margin-left:12px}
.practice .row{display:block}
.web-band{right:0;top:1150px;width:217px;height:50px}
.web{right:42px;top:1166px;font-size:15px;font-weight:500;color:var(--ink)}
</style>
</head>
<body>
<header class="abs brand">
  <div class="brand-name">CORVELITH</div>
  <div class="brand-tag">PERSONAL INJURY LAWYERS</div>
</header>

<div class="abs label prejudice">Without Prejudice</div>
<div class="abs label delivery">By Email</div>

<div class="abs clerk"><b>File Clerk:</b> <span>Nadia Fenwick</span></div>
<div class="abs clerk-email">
  <svg width="12" height="9" viewBox="0 0 12 9"><rect width="12" height="9" fill="#8ec900"/><path d="M0 0 6 5 12 0" fill="none" stroke="#f7f5f5" stroke-width="1.2"/></svg>
  nadia@corvelith.ca
</div>
<div class="abs date">March 13, 2024</div>

<address class="abs recipient" style="font-style:normal">
  Northvale Insurance Company<br>
  Claims Litigation Department<br>
  240 Brookfield Road South<br>
  P.O. Box 3100<br>
  Waterloo, ON &nbsp; N2K 7T2
</address>

<div class="abs attention">Attention: &nbsp;Mr. Owen Tarrant</div>
<div class="abs salutation">Mr. Tarrant:</div>

<div class="abs re">Re:</div>
<div class="abs matter">
  Haldane v. Moretti et al.<br>
  DOL: &nbsp;September 12, 2019<br>
  Pre-Mediation Settlement Proposal – March 13th, 2024
</div>

<div class="abs rule"></div>

<section class="abs body-copy">
  <p>Lorem ipsum dolor sit amet, consectetur adipiscing elit. Donec orci purus, luctus vitae dignissim eu, iaculis sed purus. Vivamus faucibus, ipsum nec aliquet viverra, leo mauris condimentum ligula, sit amet sagittis enim ligula quis arcu. Nam egestas tortor ivisi porttitor mattis. In tortor ante, ultricies in suscipit a, tempus non massa. Vivamus et auctor mi. Fusce vel massa nulla. Phasellus nec eros mauris, et scelerisque orci.</p>
  <p>Donec malesuada orci vitae nulla accumsan porta a id massa. Quisque accumsan iaculis magna sit amet fringilla. Maecenas consequat, magna eget tincidunt semper, odio nibh rutrum mi, id feugiat ante nisi eu risus. Vestibulum nunc orci, rhoncus a placerat in, ultricies in mi. Cras mattis varius eros, vel fringilla nisi suscipit eget. Quisque scelerisque sagittis nulla at porttitor.</p>
  <p>Sed id augue vitae urna euismod commodo aliquet a quam. Pellentesque arcu velit, cursus et malesuada ut, consequat et diam. Nullam erat sem, rhoncus id ullamcorper vitae, rhoncus et arcu. m arcu adipiscing lacus, ac bibendum nulla leo eu purus. Quisque nec diam sed risus consectetur a ccumsan quis quis nibh. Vestibulum id purus lorem.</p>
</section>

<div class="abs closing">Yours very truly,<br>CORVELITH PERSONAL INJURY LAWYERS</div>
<div class="abs signature" role="img" aria-label="Handwritten signature of the signing lawyer"></div>
<div class="abs signatory">
  Daniel P. Corvelith<br>
  Corvelith Law Professional Corporation<br>
  /nf<br>
  Encl.
</div>

<div class="abs contact">
  <div><svg width="13" height="13" viewBox="0 0 24 24"><path fill="#8ec900" d="M6.6 10.8a15.1 15.1 0 0 0 6.6 6.6l2.2-2.2c.3-.3.7-.4 1-.2 1.1.4 2.3.6 3.6.6.6 0 1 .4 1 1V20c0 .6-.4 1-1 1A17 17 0 0 1 3 4c0-.6.4-1 1-1h3.5c.6 0 1 .4 1 1 0 1.3.2 2.5.6 3.6.1.3 0 .7-.2 1z"/></svg>905-555-0142</div>
  <div><svg width="14" height="12" viewBox="0 0 14 12"><rect x="3" y="0" width="8" height="4" fill="#8ec900"/><rect x="0" y="4" width="14" height="5" rx="1" fill="#8ec900"/><rect x="3" y="8" width="8" height="4" fill="#f7f5f5" stroke="#8ec900"/></svg>905-555-0187</div>
</div>
<div class="abs office">40 Harbour Street E., Suite 1210<br>Hamilton, ON &nbsp;L8R 2B6</div>

<footer class="abs footer"></footer>
<ul class="abs practice">
  <span class="row"><li>Long-Term Disability</li><li>Serious Personal Injury</li></span>
  <span class="row"><li>Child &amp; Pediatric Injury Wrongful Death</li><li>Employee Terminations</li></span>
</ul>
<svg class="abs web-band" viewBox="0 0 217 50" preserveAspectRatio="none"><polygon points="14,0 217,0 217,50 0,50" fill="#8ec900"/></svg>
<div class="abs web">www.CORVELITH.ca</div>
</body>
</html>
```